Business card (AI file uploaded)

We need a business card design that is minimalist using existing logo (attached). Source files must be editable so we can make the same design with other names.

Screenshots included of a design I was working on to give you an idea of the style I would like. Looking for similar modern styles

Thanks

```html
<!DOCTYPE html>
<html lang="en">
<head>
<meta charset="utf-8">
<title>Marlowe Law Group – Business Card</title>
<link rel="stylesheet" href="https://fonts.googleapis.com/css2?family=Saira:wght@300;400;500&display=swap">
<style>
  :root{
    --backdrop:#d8d3d0;
    --charcoal:#3a3a3b;
    --panel-white:#f7f7f7;
    --panel-grey:#dcdcdc;
    --band-grey:#c2c2c2;
    --tab-grey:#bcbcbc;
    --silver:#8e8e8e;
    --ink-dark:#2d2d2d;
    --ink-light:#f2f2f2;
  }
  *{box-sizing:border-box;margin:0;padding:0}
  html,body{width:1200px;height:802px;overflow:hidden}
  body{background:var(--backdrop);font-family:"Saira",sans-serif;position:relative}

  .card{position:absolute;top:246px;width:540px;height:309px;overflow:hidden;
        box-shadow:0 2px 6px rgba(0,0,0,.18)}
  .card--front{left:40px}
  .card--back{left:620px}
  .card__shapes{position:absolute;inset:0;width:540px;height:309px}

  /* front */
  .brand{position:absolute;left:164px;top:68px;display:flex;align-items:center;gap:14px;color:var(--ink-dark);font-weight:400}
  .brand__dot{width:52px;height:52px;border-radius:50%;background:var(--ink-dark)}
  .brand__name{display:flex;flex-direction:column;line-height:1;text-transform:uppercase}
  .brand__primary{font-size:40px;letter-spacing:2px}
  .brand__secondary{font-size:19px;letter-spacing:6px;margin-top:4px}

  .web-tab{position:absolute;left:206px;top:186px;font-size:15px;color:var(--ink-light);letter-spacing:.5px}

  .contact{position:absolute;left:18px;color:var(--ink-light);font-size:13px;font-weight:300;line-height:1.35;display:flex;gap:10px}
  .contact svg{flex:none;margin-top:2px}
  .contact--phone{top:162px}
  .contact--address{top:212px}

  .email{position:absolute;left:196px;top:262px;display:flex;align-items:center;gap:12px;color:var(--ink-light);font-size:17px;font-weight:300;letter-spacing:.5px}

  /* back */
  .person{position:absolute;right:34px;top:34px;text-align:left;color:var(--ink-light)}
  .person__name{font-size:18px;letter-spacing:2.5px;font-weight:400;text-transform:uppercase}
  .person__title{font-size:12px;font-weight:300;letter-spacing:.5px}
  .back-web{position:absolute;right:34px;bottom:46px;color:var(--ink-light);font-size:15px;font-weight:300;letter-spacing:.5px}
</style>
</head>
<body>

<section class="card card--front" aria-label="Business card front">
  <svg class="card__shapes" viewBox="0 0 540 309" aria-hidden="true">
    <defs>
      <linearGradient id="panelFront" x1="0" y1="0" x2="1" y2="1">
        <stop offset="0" stop-color="var(--panel-white)"/>
        <stop offset="1" stop-color="var(--panel-grey)"/>
      </linearGradient>
    </defs>
    <rect width="540" height="309" fill="var(--charcoal)"/>
    <path d="M0,0 H540 V246 H196 Q176,246 176,226 V170 Q176,148 154,148 H0 Z" fill="url(#panelFront)"/>
    <path d="M0,0 H540 V26 H330 Q318,26 310,36 L304,44 H0 Z" fill="var(--band-grey)"/>
    <path d="M0,44 H304 L310,36 Q318,26 330,26 H540" fill="none" stroke="var(--silver)" stroke-width="2"/>
    <rect x="192" y="172" width="320" height="50" rx="18" fill="var(--tab-grey)"/>
    <path d="M176,226 Q176,246 196,246 H540" fill="none" stroke="var(--silver)" stroke-width="1.5"/>
  </svg>

  <div class="brand">
    <span class="brand__dot"></span>
    <span class="brand__name">
      <span class="brand__primary">Marlowe</span>
      <span class="brand__secondary">Law Group</span>
    </span>
  </div>

  <div class="web-tab">www.urwebsitename.com</div>

  <div class="contact contact--phone">
    <svg width="14" height="18" viewBox="0 0 14 18" aria-hidden="true"><path d="M3,1 L6,1 L7,5 L5,7 Q6,11 9,12 L11,10 L14,12 L13,16 Q7,17 3,11 Q0,6 3,1 Z" fill="var(--ink-light)"/></svg>
    <div>012 555 0198<br>012 555 0198</div>
  </div>

  <div class="contact contact--address">
    <svg width="20" height="16" viewBox="0 0 20 16" aria-hidden="true"><path d="M10,1 L19,8 H16 V15 H12 V10 H8 V15 H4 V8 H1 Z" fill="var(--ink-light)"/></svg>
    <div>041,12th floor,Park<br>Harbor Lane Road</div>
  </div>

  <div class="email">
    <svg width="34" height="22" viewBox="0 0 34 22" aria-hidden="true"><rect x="1" y="1" width="32" height="20" fill="none" stroke="var(--ink-light)" stroke-width="1.5"/><path d="M1,1 L17,13 L33,1 M1,21 L13,10 M33,21 L21,10" fill="none" stroke="var(--ink-light)" stroke-width="1.2"/></svg>
    <span>urname@email.com</span>
  </div>
</section>

<section class="card card--back" aria-label="Business card back">
  <svg class="card__shapes" viewBox="0 0 540 309" aria-hidden="true">
    <defs>
      <linearGradient id="panelBack" x1="0" y1="0" x2="1" y2="1">
        <stop offset="0" stop-color="var(--panel-white)"/>
        <stop offset="1" stop-color="var(--panel-grey)"/>
      </linearGradient>
    </defs>
    <rect width="540" height="309" fill="var(--charcoal)"/>
    <path d="M0,78 H128 Q150,78 150,100 V196 Q150,218 172,218 H206 V309 H0 Z" fill="url(#panelBack)"/>
    <path d="M0,250 H190 Q206,250 206,266 V309 H0 Z" fill="var(--band-grey)"/>
    <path d="M0,78 H128 Q150,78 150,100 V196 Q150,218 172,218 H206 V309" fill="none" stroke="var(--silver)" stroke-width="2"/>
  </svg>

  <div class="person">
    <div class="person__name">Daniel Whitford</div>
    <div class="person__title">Managing Director</div>
  </div>

  <div class="back-web">www.urwebsitename.com</div>
</section>

</body>
</html>
```